TL - business card

Tallow Partners is an insurance brokerage firm, inovative, proactive, vigorous, which aims to become the leader of the insurance brokers in Anfrica. We should like to get some designs which should be avoided also in Gray / Metallic for the Administration and Orange / Blue for the Managers (ike in the picture sent). The Blue / Green logo is not the correct one, but the source of the file. Please adjust the color accordingly for the business cards. 1 / Orange / Blue 2 / Gray / Metallic We want something classic but which is transmitted strenght, inovation, modernity and most of all, rapidity. We want something start-up like, very punchy and catching eye remaining profesional at the same time. Name: Dorian Whitlock Function: Managing Director Address: N ° 17/18 Rua Veloso - R / C 2B Direita - Bairro Mutamba - Luanda Tel: (+244) 947 582 316 Email: dorian.whitlock@tallow-p.example Website: www.tallow-p. example We want classic in the front and creative, colorfull at the back. The cards will be printed in relief, with very high quality of paper.
Insurance Broker
Colors
Designer to choose colors to be used in the design.

```html
<!DOCTYPE html>
<html lang="en">
<head>
<meta charset="utf-8">
<title>Tallow Partners – Business Card</title>
<link rel="stylesheet" href="https://fonts.googleapis.com/css2?family=Lato:wght@400;700;900&display=swap">
<style>
  :root {
    --brand-blue: #0b7ac2;
    --accent-red: #e0302a;
    --accent-orange: #f07a3a;
    --text-grey: #555a60;
    --rule-grey: #d2d4d6;
    --paper: #ffffff;
    --backdrop: #2b2f35;
  }
  * { box-sizing: border-box; margin: 0; padding: 0; }
  html, body {
    width: 1200px; height: 1000px; overflow: hidden;
    background: var(--backdrop);
    font-family: "Lato", Arial, sans-serif;
  }
  .canvas { position: relative; width: 1200px; height: 1000px; }
  .card {
    position: absolute; left: 215px; width: 770px; height: 440px;
    border-radius: 22px; overflow: hidden;
    box-shadow: 0 10px 24px rgba(0,0,0,.45);
  }
  /* Back side */
  .card--back { top: 50px; background: var(--brand-blue); color: var(--paper); }
  .back-mark {
    position: absolute; left: 0; right: 0; top: 170px;
    display: flex; align-items: center; justify-content: center; gap: 18px;
  }
  .mark-dot {
    flex: none; width: 46px; height: 46px; border-radius: 50%;
    border: 5px solid var(--paper);
  }
  .back-name {
    font-weight: 900; font-size: 46px; letter-spacing: 1px; text-transform: uppercase; white-space: nowrap;
  }
  .back-url {
    position: absolute; left: 0; right: 0; top: 330px;
    text-align: center; font-size: 19px; letter-spacing: .5px;
  }
  /* Front side */
  .card--front { top: 510px; background: var(--brand-blue); }
  .front-shape { position: absolute; inset: 0; }
  .holder { position: absolute; left: 58px; top: 170px; width: 320px; }
  .holder-name {
    color: var(--accent-red); font-weight: 900; font-size: 32px; letter-spacing: 1px; white-space: nowrap;
  }
  .holder-role {
    color: var(--text-grey); font-size: 20px; margin-top: 2px; letter-spacing: .5px;
  }
  .divider {
    position: absolute; left: 40px; top: 272px; width: 660px; height: 1px;
    background: linear-gradient(90deg, var(--accent-red) 0, var(--accent-orange) 27%, var(--rule-grey) 28%);
  }
  .contacts {
    position: absolute; left: 50px; top: 292px; list-style: none;
    color: var(--text-grey); font-size: 19px; letter-spacing: .3px;
  }
  .contacts li { display: flex; align-items: center; gap: 14px; height: 36px; white-space: nowrap; }
  .contacts svg { width: 18px; height: 18px; flex: none; }
  .front-mark {
    position: absolute; right: 50px; top: 180px;
    display: flex; align-items: center; gap: 12px;
  }
  .front-mark .mark-dot { border-color: var(--accent-orange); width: 36px; height: 36px; border-width: 4px; }
  .front-name {
    color: var(--brand-blue); font-weight: 900; font-size: 26px; letter-spacing: 1px;
    text-transform: uppercase; white-space: nowrap;
  }
  .address {
    position: absolute; right: 48px; top: 350px; text-align: right; font-style: normal;
    color: var(--text-grey); font-size: 18px; line-height: 1.4; letter-spacing: .3px; white-space: nowrap;
  }
</style>
</head>
<body>
<main class="canvas">

  <section class="card card--back" aria-label="Card back">
    <div class="back-mark">
      <span class="mark-dot"></span>
      <span class="back-name">Tallow Partners</span>
    </div>
    <p class="back-url">www.tallow-p. example</p>
  </section>

  <section class="card card--front" aria-label="Card front">
    <svg class="front-shape" viewBox="0 0 770 440" preserveAspectRatio="none" aria-hidden="true">
      <defs>
        <linearGradient id="swoosh" x1="0" x2="1" y1="0" y2="0">
          <stop offset="0" stop-color="#f07a3a" stop-opacity="0"/>
          <stop offset=".35" stop-color="#f07a3a"/>
          <stop offset="1" stop-color="#e0302a"/>
        </linearGradient>
      </defs>
      <path d="M0,72 C260,78 540,108 770,165 L770,440 L0,440 Z" fill="#ffffff"/>
      <path d="M150,80 C400,92 600,118 770,140 L770,158 C560,110 330,84 150,80 Z" fill="url(#swoosh)"/>
    </svg>

    <div class="holder">
      <h1 class="holder-name">Dorian Whitlock</h1>
      <p class="holder-role">Managing Director</p>
    </div>

    <div class="divider"></div>

    <ul class="contacts">
      <li>
        <svg viewBox="0 0 24 24" fill="#e0452c"><path d="M6.6 10.8a15.1 15.1 0 0 0 6.6 6.6l2.2-2.2c.3-.3.7-.4 1-.2 1.1.4 2.3.6 3.6.6.6 0 1 .4 1 1V20c0 .6-.4 1-1 1A17 17 0 0 1 3 4c0-.6.4-1 1-1h3.5c.6 0 1 .4 1 1 0 1.3.2 2.5.6 3.6.1.3 0 .7-.2 1z"/></svg>
        <span>(+244) 947 582 316</span>
      </li>
      <li>
        <svg viewBox="0 0 24 24"><rect x="2" y="5" width="20" height="14" rx="1.5" fill="#e0452c"/><path d="M3 6l9 7 9-7" fill="none" stroke="#fff" stroke-width="2"/></svg>
        <span>dorian.whitlock@tallow-p.example</span>
      </li>
      <li>
        <svg viewBox="0 0 24 24" fill="none" stroke="#e0452c" stroke-width="2"><circle cx="12" cy="12" r="9"/><path d="M3 12h18M12 3c3 3 3 15 0 18M12 3c-3 3-3 15 0 18"/></svg>
        <span>www.tallow-p. example</span>
      </li>
    </ul>

    <div class="front-mark">
      <span class="mark-dot"></span>
      <span class="front-name">Tallow Partners</span>
    </div>

    <address class="address">
      N ° 17/18 Rua Veloso - R / C 2B<br>
      Direita - Bairro Mutamba - Luanda
    </address>
  </section>

</main>
</body>
</html>
```